Stylish Business Cards Wanted

- DOUBLE SIDED Design Required -

High end, edgy cards for a corporate and personal stylist. Must include logo,
Name: Belinda Harwick
Title: Director and Stylist
telephone : +61 8 7142 5809
email: belinda@theloombriefing.example
website: theloombriefing.example
Tag: Corporate Workwear & Uniform Specialist | Personal Stylist
Would like nice icons for telephone, email, website

Target Market(s)

Businesses wanting stylish uniforms, people wanting stylish wardrobes

Industry/Entity Type

Corporate Workwear Stylist

Contact Information for Business Card

I would like black, white and gold foiling incorporated in the design - possibly a touch of the other colours on my branding guide attached Name: Belinda Harwick Title: Director and Stylist telephone : +61 8 7142 5809 email: belinda@theloombriefing.example website: theloombriefing.example Tag: Corporate Workwear & Uniform Specialist | Personal Stylist Would like nice icons for telephone, email, website

Font styles to use
Other font styles liked:
• Raleway

Colors

Designer to choose colors to be used in the design.

Requirements
Must have
• Gold foil accents

```html
<!DOCTYPE html>
<html lang="en">
<head>
<meta charset="utf-8">
<title>The Loom Briefing – Business Cards</title>
<link rel="stylesheet" href="https://fonts.googleapis.com/css2?family=Raleway:wght@400;600&family=Roboto:wght@400&family=Courgette&display=swap">
<style>
  :root {
    --backdrop: #c9c9c9;
    --card-navy: #141b30;
    --gold: #d9ae45;
    --white: #f2f2f2;
    --plum: #7a2a52;
  }
  * { margin: 0; padding: 0; box-sizing: border-box; }
  html, body {
    width: 1200px; height: 852px; overflow: hidden;
    background: var(--backdrop);
  }
  .stage { position: relative; width: 1200px; height: 852px; }
  .card {
    position: absolute;
    width: 620px; height: 354px;
    background: var(--card-navy);
    border-radius: 26px;
    overflow: hidden;
  }
  .card--front { left: 150px; top: 70px; }
  .card--back { left: 430px; top: 430px; }

  .wordmark {
    font-family: "Raleway", sans-serif;
    font-weight: 600;
    letter-spacing: 1px;
    display: flex; align-items: center; gap: 12px;
    white-space: nowrap;
  }
  .wordmark__dot {
    width: 14px; height: 14px; border-radius: 50%; flex: none;
  }
  .card--front .wordmark {
    position: absolute; left: 0; right: 0; top: 0; bottom: 0;
    justify-content: center;
    color: var(--gold); font-size: 40px;
  }
  .card--front .wordmark__dot { background: var(--gold); }

  .card--back .wordmark {
    position: absolute; left: 28px; top: 154px;
    width: 220px;
    color: var(--white); font-size: 19px; gap: 9px;
    letter-spacing: 0.5px;
  }
  .card--back .wordmark__dot { background: var(--white); width: 9px; height: 9px; }

  .divider {
    position: absolute; left: 270px; top: 78px;
    width: 1px; height: 150px; background: var(--plum);
  }
  .contact { position: absolute; left: 302px; top: 74px; }
  .contact__name {
    font-family: "Courgette", cursive;
    font-weight: 400;
    color: var(--gold); font-size: 27px; line-height: 1;
  }
  .contact__title {
    font-family: "Roboto", sans-serif;
    color: var(--white); font-size: 14px; margin: 8px 0 14px 14px;
  }
  .contact__list { list-style: none; }
  .contact__item {
    display: flex; align-items: center; gap: 12px;
    font-family: "Roboto", sans-serif; font-size: 14px;
    color: var(--white); margin-bottom: 5px; margin-left: 14px;
    white-space: nowrap;
  }
  .contact__item svg { width: 14px; height: 14px; flex: none; }
  .tagline {
    position: absolute; left: 0; right: 0; bottom: 30px;
    text-align: center;
    font-family: "Courgette", cursive;
    color: var(--white); font-size: 17px; letter-spacing: 0.3px;
    white-space: nowrap;
  }
</style>
</head>
<body>
<main class="stage">
  <section class="card card--front" aria-label="Card front">
    <div class="wordmark"><span class="wordmark__dot"></span>The Loom Briefing</div>
  </section>

  <section class="card card--back" aria-label="Card back">
    <div class="wordmark"><span class="wordmark__dot"></span>The Loom Briefing</div>
    <div class="divider"></div>
    <div class="contact">
      <h1 class="contact__name">Belinda Harwick</h1>
      <p class="contact__title">Director and Stylist</p>
      <ul class="contact__list">
        <li class="contact__item">
          <svg viewBox="0 0 16 16" aria-hidden="true"><circle cx="8" cy="8" r="7" fill="none" stroke="#d9ae45" stroke-width="1.4"/><path d="M5.5 4.5l1.3 1.6-.8 1c.6 1.2 1.5 2.1 2.7 2.7l1-.8 1.6 1.3-.7 1.1c-2.9-.5-5.2-2.8-5.7-5.7z" fill="#d9ae45"/></svg>
          +61 8 7142 5809
        </li>
        <li class="contact__item">
          <svg viewBox="0 0 16 16" aria-hidden="true"><rect x="1.5" y="3.5" width="13" height="9" rx="1" fill="none" stroke="#d9ae45" stroke-width="1.4"/><path d="M2 4l6 5 6-5" fill="none" stroke="#d9ae45" stroke-width="1.4"/></svg>
          belinda@theloombriefing.example
        </li>
        <li class="contact__item">
          <svg viewBox="0 0 16 16" aria-hidden="true"><circle cx="8" cy="8" r="6.5" fill="none" stroke="#d9ae45" stroke-width="1.3"/><ellipse cx="8" cy="8" rx="2.8" ry="6.5" fill="none" stroke="#d9ae45" stroke-width="1.1"/><path d="M1.5 8h13M2.5 5h11M2.5 11h11" stroke="#d9ae45" stroke-width="1"/></svg>
          www.theloombriefing.example
        </li>
      </ul>
    </div>
    <p class="tagline">Corporate Workwear &amp; Uniform Specialist &nbsp;|&nbsp; Personal Stylist</p>
  </section>
</main>
</body>
</html>
```